Graphic Design Project

We make rose petal jelly from old fashioned english roses. The jelly is sweet eaten with scones and clotted cream or as a filling in a victoria sandwich, as a topping on ice cream or thick set yogurt.
The image of the product is luxurious and decadent and very english.
We need a design for a label which has a picture of an old fashioned rose (rosa mundi or a compte de chambard) The rose must stand out clearly so the jelly is not confused with other fruit jams. The overall colour of the label should be pink and soft, with white or dark pink writing. The label needs to be fridge proof.

We also need a security strip to fit on the lid of the jar.

We need the following information on the label.
Name of our company-"Meadow Crown"
Name of Product-"Rose Petal Jelly"
Sales pitch-"With whole petals-a taste of summer, delicious on scones, as a filling in sponge cake, as a topping on ice cream or yogurt."
INGREDIENTS: Sugar, water, rose petals, lemon juice, natural jelling agent (agar-agar)
STORAGE: Store in a cool dry place, once opened keep refrigerated and consume within 4 weeks.
BEST BEFORE: See base

200g
Produced by:
MEADOW CROWN
The Larches
Pardew Lane
Ashcombe
Westvaleshire
GL17 4RX
The label must have room for a bar code. The size of label approx 8-10cm long 5cm wide.
Updates

Hi

Just been looking at the Hartwell and Brace site and the labels they have there have the up market feel I am trying to convey. Hope that helps, its classy but not twee.

Thanks

Thanks for all submissions. I would be grateful if you googled images for 'Colourful and expensive biscuits at Hartwell Brace' The designs on the tins are the image we are trying to create. The colours are quite strong.

Thanks

Target Market(s)

older well off people who visit garden centres

Industry/Entity Type

Security

Requirements
Must have
• All writen info above and picture of old fashioned rose prferably rose a mundi. Luxury feel, very english, to appeal to older market
Pink colour sheme
Should not have
• dark or manly colours

```html
<!DOCTYPE html>
<html lang="en">
<head>
<meta charset="utf-8">
<title>Meadow Crown – Rose Petal Jelly Label</title>
<link rel="stylesheet" href="https://fonts.googleapis.com/css2?family=Sorts+Mill+Goudy&display=swap">
<style>
  :root {
    --label-pink: #d6006a;
    --petal-light: #f48dc6;
    --petal-soft: #f6a9d2;
    --cream-white: #ffffff;
    --plum-text: #8c1452;
    --rose-deep: #b01a9a;
    --rose-bright: #d23ad0;
    --box-line: #555555;
  }
  * { margin: 0; padding: 0; box-sizing: border-box; }
  html, body {
    width: 1200px;
    height: 750px;
    overflow: hidden;
    background: var(--cream-white);
  }
  .label {
    position: relative;
    width: 1200px;
    height: 750px;
    font-family: "Sorts Mill Goudy", Georgia, serif;
    overflow: hidden;
  }
  .front-panel {
    position: absolute;
    left: 0; top: 0;
    width: 797px;
    height: 750px;
    background: var(--label-pink);
    text-align: center;
  }
  .brand-name {
    position: absolute;
    left: 0; right: 0;
    top: 36px;
    font-size: 54px;
    font-weight: 400;
    color: var(--petal-light);
    line-height: 1;
    padding-left: 15px;
  }
  .product-name {
    position: absolute;
    left: 0; right: 0;
    top: 114px;
    font-size: 75px;
    font-weight: 400;
    color: var(--cream-white);
    line-height: 1;
    padding-left: 15px;
  }
  .strapline {
    position: absolute;
    left: 0; right: 0;
    top: 198px;
    font-size: 27.5px;
    color: var(--petal-soft);
    padding-left: 15px;
    white-space: nowrap;
  }
  .rose-art {
    position: absolute;
    left: 252px;
    top: 272px;
    width: 282px;
    height: 278px;
    border-radius: 46%;
    background: radial-gradient(circle at 50% 50%, var(--rose-deep) 0%, var(--rose-bright) 55%, #c629b8 78%, rgba(214,0,106,0) 100%);
  }
  .serving-ideas {
    position: absolute;
    left: 0; right: 0;
    top: 580px;
    font-size: 31px;
    line-height: 40px;
    color: var(--petal-soft);
    padding-left: 15px;
  }
  .net-weight {
    position: absolute;
    left: 612px;
    top: 701px;
    font-size: 36px;
    color: var(--cream-white);
    line-height: 1;
  }
  .info-panel {
    position: absolute;
    left: 816px;
    top: 26px;
    width: 384px;
    color: var(--plum-text);
  }
  .info-block {
    font-size: 23.5px;
    line-height: 30.5px;
    white-space: nowrap;
  }
  .ingredients { margin-bottom: 37px; }
  .storage { margin-bottom: 30px; }
  .best-before { margin-bottom: 28px; padding-left: 2px; }
  .producer {
    font-size: 28px;
    line-height: 35.5px;
    font-style: normal;
  }
  .barcode-space {
    position: absolute;
    left: 1002px;
    top: 637px;
    width: 174px;
    height: 89px;
    border: 1.5px solid var(--box-line);
    border-radius: 3px;
    background: var(--cream-white);
    font-family: Arial, Helvetica, sans-serif;
    font-size: 17px;
    line-height: 25px;
    color: #000000;
    padding: 18px 0 0 6px;
  }
</style>
</head>
<body>
  <main class="label">
    <section class="front-panel">
      <p class="brand-name">Meadow Crown</p>
      <h1 class="product-name">Rose Petal Jelly</h1>
      <p class="strapline">"With whole petals its a taste of summer”</p>
      <div class="rose-art" role="img" aria-label="Photograph of four old fashioned magenta English roses"></div>
      <p class="serving-ideas">Delicious on scones, as a filling<br>in sponge cake, as a topping<br>on ice cream or yogurt.</p>
      <p class="net-weight">200g</p>
    </section>

    <section class="info-panel">
      <p class="info-block ingredients">INGREDIENTS:<br>Sugar, water, rose petals, lemon<br>juice, natural jelling agent (agar-agar)</p>
      <p class="info-block storage">STORAGE: Store in a cool dry<br>place, once opened keep refrigerated<br>and consume within 4 weeks.</p>
      <p class="info-block best-before">BEST BEFORE:<br>See base</p>
      <address class="producer">
        Produced by:<br>
        MEADOW CROWN<br>
        The Larches<br>
        Pardew Lane<br>
        Ashcombe<br>
        Westvaleshire<br>
        GL17 4RX
      </address>
    </section>

    <div class="barcode-space">Bar<br>Code</div>
  </main>
</body>
</html>
```